Allied Health team of Physiotherapists & Occupational Therapists seek a business card design

We have our new logo, we now need our new business cards and stationary. Tidewell: Oedema & Family Clinic is seeking a generic card design to represent our whole team and individual cards for each therapist that incorporates our new logo to communicate our holistic approach that is calming, nuturing, supportive and welcoming.
Our Physiotherapists and Occupational Therapists assess, treat and provide education for people who are at risk of or who have lymphoedema. This is often as a result of treatment for cancer. We provide pre-operative and post-operative management and cancer rehabilitation in our Pilates studio. Our team also consists of Physiotherapists who have a strong interest in pelvic floor and continence management for both men and women.

Target Market(s)

Mainly women health conscious

Industry/Entity Type

Allied Health: Physiotherapy / Occupational Therapy

Contact Information for Business Card

Address: 14 Gallivant Ave Frankston 3199 Phone: 84316570 fax: 8431 6578 Email: info@tidewellcareservices.com.au Website: tidewellcareservices.com.au Facebook address: facebook.com/TidewellOedemaAndFamilyCareClinic. Room to write appointments. Individual cards need to have name, office email and individual email and professional details

Requirements
Must have
• Logo as per uploaded documents

```html
<!DOCTYPE html>
<html lang="en">
<head>
<meta charset="utf-8">
<title>Tidewell: Oedema &amp; Family Clinic — Business Card</title>
<link href="https://fonts.googleapis.com/css2?family=Arimo:wght@400;700&display=swap" rel="stylesheet">
<style>
  :root {
    --backdrop: #262626;
    --peach: #f8b286;
    --white: #ffffff;
    --sage: #c3cbc1;
    --shadow: rgba(0, 0, 0, 0.45);
  }
  * { margin: 0; padding: 0; box-sizing: border-box; }
  html, body {
    width: 1200px; height: 880px; overflow: hidden;
    background: var(--backdrop);
    font-family: "Arimo", Arial, sans-serif;
  }
  .canvas { position: relative; width: 1200px; height: 880px; }
  .card {
    position: absolute; left: 260px; width: 680px; height: 390px;
    border-radius: 26px; overflow: hidden;
    box-shadow: 0 14px 30px var(--shadow);
  }
  .card--front { top: 35px; background: var(--peach); }
  .card--back { top: 455px; background: var(--peach); }
  .card__art { position: absolute; inset: 0; }

  .brand {
    position: absolute; display: flex; flex-direction: column;
    align-items: center; gap: 10px; text-align: center;
    font-weight: 400; font-size: 17px; line-height: 1.3; letter-spacing: 0.06em;
  }
  .brand__dot { width: 16px; height: 16px; border-radius: 50%; }
  .card--front .brand { left: 0; right: 0; top: 160px; color: var(--white); }
  .card--front .brand__dot { background: var(--white); }
  .card--back .brand { left: 40px; width: 250px; top: 160px; color: var(--peach); }
  .card--back .brand__dot { background: var(--peach); }

  .contact {
    position: absolute; left: 440px; top: 48px; width: 230px;
    color: var(--white);
  }
  .contact__name { font-weight: 700; font-size: 20px; letter-spacing: 0.16em; }
  .contact__role { font-size: 11px; margin-top: 3px; }
  .contact__address { font-size: 15px; line-height: 1.35; margin-top: 36px; }
  .contact__list { list-style: none; margin-top: 36px; }
  .contact__item {
    display: flex; align-items: center; gap: 12px;
    font-size: 15px; line-height: 1; margin-bottom: 14px; white-space: nowrap;
  }
  .contact__item--small { font-size: 12.5px; }
  .contact__icon { width: 18px; height: 18px; flex: none; }
</style>
</head>
<body>
<main class="canvas">

  <section class="card card--front" aria-label="Business card front">
    <div class="brand">
      <span class="brand__dot"></span>
      <span class="brand__name">Tidewell: Oedema<br>&amp; Family Clinic</span>
    </div>
  </section>

  <section class="card card--back" aria-label="Business card back">
    <svg class="card__art" width="680" height="390" viewBox="0 0 680 390" aria-hidden="true">
      <circle cx="172" cy="240" r="266" fill="var(--white)"/>
      <circle cx="168" cy="240" r="264" fill="var(--sage)"/>
      <circle cx="153" cy="240" r="262" fill="var(--white)"/>
    </svg>

    <div class="brand">
      <span class="brand__dot"></span>
      <span class="brand__name">Tidewell: Oedema<br>&amp; Family Clinic</span>
    </div>

    <div class="contact">
      <p class="contact__name">MARA ELLWOOD</p>
      <p class="contact__role">CEO/Managing Director</p>
      <p class="contact__address">14 Gallivant Ave<br>Frankston, VIC 3199</p>
      <ul class="contact__list">
        <li class="contact__item">
          <svg class="contact__icon" viewBox="0 0 24 24" aria-hidden="true"><path fill="#fff" d="M6.6 10.8a15.2 15.2 0 0 0 6.6 6.6l2.2-2.2c.3-.3.7-.4 1-.2 1.1.4 2.3.6 3.6.6.6 0 1 .4 1 1V20c0 .6-.4 1-1 1A17 17 0 0 1 3 4c0-.6.4-1 1-1h3.5c.6 0 1 .4 1 1 0 1.3.2 2.5.6 3.6.1.3 0 .7-.2 1z"/></svg>
          8431 6570
        </li>
        <li class="contact__item">
          <svg class="contact__icon" viewBox="0 0 24 24" aria-hidden="true"><rect x="6" y="2" width="12" height="20" rx="2" fill="none" stroke="#fff" stroke-width="2"/><circle cx="12" cy="18" r="1.2" fill="#fff"/></svg>
          8431 6578
        </li>
        <li class="contact__item contact__item--small">
          <svg class="contact__icon" viewBox="0 0 24 24" aria-hidden="true"><rect x="2" y="5" width="20" height="14" fill="#fff"/><path d="M2 5l10 8 10-8" fill="none" stroke="var(--peach)" stroke-width="1.6"/></svg>
          info@tidewellcareservices.com.au
        </li>
        <li class="contact__item contact__item--small">
          <svg class="contact__icon" viewBox="0 0 24 24" aria-hidden="true"><g fill="none" stroke="#fff" stroke-width="1.8"><circle cx="12" cy="12" r="9.5"/><ellipse cx="12" cy="12" rx="4" ry="9.5"/><path d="M2.5 12h19M4 7h16M4 17h16"/></g></svg>
          tidewellcareservices.com.au
        </li>
      </ul>
    </div>
  </section>

</main>
</body>
</html>
```